Verpackungsdesign für Wellness- und Saunaprodukte
Zielgruppe
BaFinn ist ein junges Start-Up, das sich auf Wellness- und Saunaprodukte spezialisiert hat. Unsere Zielgruppe besteht zu beinahe gleichen Teilen aus männlichen und weiblichen Personen zwischen 30 und 60 Jahren. Unsere Produkte befinden sich eher im mittel- bis höherpreisigen Segment, daher streben wir ein hochwertiges Design für unsere Verpackungen an. Unsere Produktpalette reicht von Mentholkristallen, Saunaaufgüssen, bis hin zu Textilien für den Wellnessbereich und soll dementsprechend Menschen ansprechen, die sich einen gewissen Luxus im Alltag auch gönnen.
Aufgabenstellung
Inspiriert von der skandinavischen Sauna Kultur, möchten wir Momente der Erholung und
Entspannung in den Alltag unserer Kunden bringen. Die Geschichte des Saunierens ist eng mit der skandinavischen Kultur verbunden und skandinavische Stilelemente sind zeitgemäß und sprechen ein breites Publikum an. Das Design muss auf Dosen/Tiegel , Karton Verpackungen und Flaschen verschiedener Größen adaptierbar sein (siehe Bild im Anhang).
40g Tiegel(transparent) Höhe 40mm Durchmesser 60mm (ohne Deckel Silber gebürstet)
100g Tiegel(transparent) Höhe 53mm Durchmesser 71mm (ohne Deckel Silber gebürstet)
200g Tiegel(transparent) Höhe 65mm Durchmesser 90mm (ohne Deckel Silber gebürstet)
Karton Verpackung 124,5x49x49mm
Karton Verpackung 100x100x100mm
Flaschenetikett 134x67mm (Braunglas, schwarzer Deckel)
Es soll ein passendes Keyvisual erstellt werden.
Im Anhang sieht man die Verpackungen, Dosen, Flaschen sowie unsere ersten Design Entwürfe (an diese Anordnung der Elemente kann sich der Designer orientieren ). Das Logo bleibt wie gegeben. Das Produkt für die Tiegel soll Mentholkristalle sein.

```html
<!DOCTYPE html>
<html lang="de">
<head>
<meta charset="utf-8">
<title>BaFinn – Mentholkristalle</title>
<link href="https://fonts.googleapis.com/css2?family=Libre+Baskerville:wght@400;700&display=swap" rel="stylesheet">
<style>
  :root {
    --page-white: #ffffff;
    --stage-top: #efefef;
    --stage-bottom: #f5f5f5;
    --box-top: #f2f2f2;
    --box-bottom: #e6e6e6;
    --box-edge: #c4c4c4;
    --notch: #c9c9c9;
    --lid-light: #dcdcdc;
    --lid-mid: #b8b8b8;
    --lid-edge: #a9a9a9;
    --jar-light: #f3f2f2;
    --jar-shade: #e4e2e2;
    --text-grey: #a3a3a3;
    --brand-grey: #8f8f8f;
    --teal: #1f8f84;
    --teal-dark: #116a62;
  }
  html, body {
    margin: 0;
    padding: 0;
    width: 1200px;
    height: 1200px;
    overflow: hidden;
    background: var(--page-white);
  }
  .canvas {
    position: relative;
    width: 1200px;
    height: 1200px;
  }
  .stage {
    position: absolute;
    left: 0;
    top: 122px;
    width: 1200px;
    height: 956px;
    background: linear-gradient(180deg, var(--stage-top), var(--stage-bottom));
  }

  /* Faltschachtel */
  .carton {
    position: absolute;
    left: 368px;
    top: 500px;
    width: 346px;
    height: 318px;
    background: linear-gradient(160deg, var(--box-top), var(--box-bottom));
    border-top: 3px solid var(--box-edge);
    border-bottom: 2px solid #d0d0d0;
    box-sizing: border-box;
    box-shadow: 0 6px 10px rgba(0,0,0,0.05);
  }
  .carton-notch {
    position: absolute;
    left: 141px;
    top: 0;
    width: 70px;
    height: 19px;
    background: var(--notch);
    border-radius: 0 0 35px 35px / 0 0 19px 19px;
  }
  .carton .brand {
    position: absolute;
    top: 75px;
    left: 0;
    width: 100%;
    text-align: center;
    font-family: "Libre Baskerville", serif;
    font-weight: 400;
    font-size: 14px;
    letter-spacing: 0.5px;
    color: var(--brand-grey);
  }
  .carton .product-name {
    position: absolute;
    top: 155px;
    left: 0;
    width: 100%;
    margin: 0;
    text-align: center;
    font-family: "Libre Baskerville", serif;
    font-weight: 700;
    font-size: 20px;
    color: var(--text-grey);
  }
  .carton .emblem {
    position: absolute;
    left: 146px;
    top: 215px;
    width: 54px;
    height: 54px;
  }

  /* Tiegel */
  .jar {
    position: absolute;
    left: 648px;
    top: 614px;
    width: 262px;
    height: 224px;
  }
  .jar-lid {
    position: absolute;
    left: 0;
    top: 0;
    width: 262px;
    height: 63px;
    border-radius: 4px 4px 0 0;
    background: linear-gradient(90deg, var(--lid-light) 0%, var(--lid-mid) 45%, #d4d4d4 70%, var(--lid-mid) 100%);
    border-bottom: 2px solid var(--lid-edge);
    box-sizing: border-box;
  }
  .jar-body {
    position: absolute;
    left: 0;
    top: 64px;
    width: 262px;
    height: 160px;
    border-radius: 4px 4px 26px 26px;
    background: linear-gradient(90deg, var(--jar-light) 0%, var(--jar-shade) 60%, #ecebeb 100%);
    box-shadow: 0 4px 8px rgba(0,0,0,0.07);
  }
  .jar .brand {
    position: absolute;
    top: 26px;
    left: 0;
    width: 100%;
    text-align: center;
    font-family: "Libre Baskerville", serif;
    font-weight: 400;
    font-size: 8px;
    color: var(--brand-grey);
  }
  .jar .product-name {
    position: absolute;
    top: 58px;
    left: 0;
    width: 100%;
    margin: 0;
    text-align: center;
    font-family: "Libre Baskerville", serif;
    font-weight: 700;
    font-size: 13px;
    color: var(--text-grey);
  }
  .jar .emblem {
    position: absolute;
    left: 116px;
    top: 96px;
    width: 30px;
    height: 30px;
  }

  .emblem {
    border-radius: 50%;
    background: radial-gradient(circle at 40% 35%, var(--teal), var(--teal-dark));
  }
</style>
</head>
<body>
  <div class="canvas">
    <div class="stage"></div>

    <div class="carton">
      <div class="carton-notch"></div>
      <div class="brand">BaFinn</div>
      <h1 class="product-name">Mentholkristalle</h1>
      <div class="emblem" role="img" aria-label="Türkises rundes Emblem mit skandinavischem Schneekristall-Muster"></div>
    </div>

    <div class="jar">
      <div class="jar-lid"></div>
      <div class="jar-body">
        <div class="brand">BaFinn</div>
        <h2 class="product-name">Mentholkristalle</h2>
        <div class="emblem" role="img" aria-label="Kleines türkises Emblem mit Schneekristall-Muster"></div>
      </div>
    </div>
  </div>
</body>
</html>
```